Brief 1.
An Overview / Background of the Business & Services-
It is a new business being set up. Our business is to design a solution to enable Alumni of higher institutions in Nigeria apply for their academic transcript through our system. the name of our product will be Record Relay Nigeria. We need logo, site banner, advert banner and several academic images. See www.rrly-ng.example for more insight.
The Target Market / Audience you are trying to reach-
Alumni of Nigeria Universities, usually between the ages of 20-40.
Design Specifics; any preferences or ideas for Style, Colour, Imagery, etc-
Color scheme will be several shades of light blue and white. Please check www.rrly-ng.example for more insight.

Brief 2

Pantrybasket.com is an online food and grocery shop, we supply fresh food stuff and other daily essential needs on request to customers. The site is already up (www.pantrybasket.example). We need logo, site rolling banner, advert banner and several offer graphics as shown in the placeholder images in the site now.
Working women in Nigeria.
Color scheme will be several shades of light Green and White. Please check the site.

```html
<!DOCTYPE html>
<html lang="en">
<head>
<meta charset="utf-8">
<title>Pantrybasket.com – Feed well, live well</title>
<link href="https://fonts.googleapis.com/css2?family=Open+Sans:wght@400;600;700&family=Roboto+Slab:wght@400;700&family=Montserrat:wght@600;700&display=swap" rel="stylesheet">
<style>
:root{
  --green:#6cb42c;
  --green-dark:#4c8f1a;
  --green-deep:#3f7d12;
  --lime:#8cc63f;
  --teal:#27a39a;
  --blue:#3aa0c9;
  --link-blue:#3f8fd0;
  --text:#555;
  --text-dark:#333;
  --line:#e4e4e4;
  --card-border:#e6e6e6;
  --page-bg:#f7f7f5;
  --white:#fff;
  --red:#d0021b;
  --black:#111;
}
*{box-sizing:border-box;margin:0;padding:0}
html,body{width:1200px;height:2341px;overflow:hidden}
body{background:var(--page-bg);font-family:"Open Sans",Arial,sans-serif;color:var(--text);font-size:13px}
.page{position:relative;width:1200px;height:2341px}
.abs{position:absolute}

/* header */
.logo{left:125px;top:48px;display:flex;align-items:center;gap:14px}
.logo-mark{width:52px;height:52px;background:var(--green)}
.logo-name{font-family:"Montserrat",Arial,sans-serif;font-weight:700;font-size:34px;color:var(--green);letter-spacing:1px}
.search{left:509px;top:62px;width:220px;height:35px;background:var(--white);border:1px solid #ddd;outline:3px solid #efefef;display:flex;align-items:center;padding:0 10px;font-size:12px;color:#777;justify-content:space-between}
.cart-mini{left:925px;top:76px;display:flex;align-items:center;gap:6px;font-size:13px}
.cart-mini .items{color:var(--link-blue)}
.cart-mini .sum{color:var(--text-dark)}

/* nav */
.nav{left:90px;top:131px;width:1002px;height:52px}
.nav-links{left:125px;top:131px;width:960px;height:50px}
.nav-links a{position:absolute;top:0;height:50px;line-height:50px;color:var(--white);font-family:"Roboto Slab",Georgia,serif;font-weight:700;font-size:14px;text-decoration:none;white-space:nowrap}
.nav-links a.active{background:var(--green-deep);padding:0 16px}
.welcome{left:125px;top:186px;width:949px;height:30px;background:var(--white);border:1px solid var(--line);border-top:none;display:flex;justify-content:space-between;align-items:center;padding:0 16px;font-size:12.5px}
.welcome .links span{margin:0 4px}

/* main container */
.main{left:125px;top:234px;width:949px;height:1716px;background:var(--white);border:1px solid var(--line)}

.slider{left:142px;top:257px;width:669px;height:378px;border:1px solid #ddd;background:linear-gradient(90deg,#f2f2f2,#e7e7e7 60%,#dcdcdc)}
.slider .photo{left:0;top:0;width:370px;height:376px;background:radial-gradient(ellipse at 45% 55%,#d9a23b 0,#8fae3a 30%,#c9c9c9 62%,#ececec 80%)}
.headline{left:360px;top:98px;width:274px;text-align:right;font-family:"Montserrat",Arial,sans-serif;font-weight:700;font-size:47px;line-height:52px;color:var(--green)}
.headline .teal{color:var(--teal)}
.sub-headline{left:360px;top:202px;width:274px;text-align:right;font-family:"Montserrat",Arial,sans-serif;font-weight:600;font-size:17px;color:var(--text-dark)}
.btn-shop{left:510px;top:252px;width:123px;height:43px;background:var(--lime);color:var(--white);font-size:14px;line-height:43px;text-align:center;font-weight:600}
.dots{left:304px;top:350px;display:flex;gap:6px}
.dots i{width:11px;height:11px;border-radius:50%;background:#222;display:block}
.dots i.on{background:var(--lime)}

.promo{left:821px;width:235px;border:1px solid #ddd}
.promo-delivery{top:257px;height:183px;background:linear-gradient(180deg,#fbfde9,#eef7c9)}
.promo-delivery .title{top:22px;width:100%;text-align:center;font-size:18px;line-height:28px;color:var(--text-dark)}
.promo-delivery .note{top:95px;width:100%;text-align:center;font-size:14px;color:var(--link-blue)}
.promo-delivery .strip{left:0;top:142px;width:100%;height:24px;background:var(--lime);font-size:12px;color:#333;padding-left:30px;line-height:24px}
.seal{left:190px;top:132px;width:40px;height:40px;border-radius:50%;background:var(--teal);color:var(--white);font-size:10px;font-weight:700;text-align:center;line-height:40px}
.promo-spa{top:449px;height:186px;background:#f4f9ec}
.promo-spa .title{top:20px;width:100%;text-align:center;font-size:16px;line-height:22px;color:var(--text-dark)}
.promo-spa .photo{left:0;top:66px;width:233px;height:118px;background:linear-gradient(180deg,#f7f2dc,#e8d27a 70%,#d6b948)}

/* sidebar */
.side-head{left:125px;width:216px;height:35px;background:var(--green);clip-path:polygon(0 0,94% 0,100% 50%,94% 100%,0 100%);color:var(--white);font-family:"Roboto Slab",Georgia,serif;font-weight:700;font-size:14px;line-height:35px;padding-left:20px}
.side-head.blue{background:var(--blue)}
.cat-list{left:142px;top:710px;width:192px;list-style:none}
.cat-list li{height:29.5px;line-height:29px;border-bottom:1px solid var(--line);font-size:13px;display:flex;justify-content:space-between;padding:0 4px}
.side-note{left:155px;width:180px;font-size:12.5px;line-height:20px}
.hurry{left:142px;top:1151px;width:200px;height:253px;background:var(--white);border:1px solid #eee}
.hurry .title{left:14px;top:10px;font-family:"Roboto Slab",Georgia,serif;font-weight:700;font-size:21px;line-height:27px;color:var(--green)}
.hurry .photo{left:0;top:73px;width:198px;height:178px;background:radial-gradient(circle at 40% 50%,#d73a1f 0,#e86b22 25%,#7aa83a 55%,#c7b28b 85%)}
.badge-off{left:136px;top:80px;width:56px;height:56px;border-radius:50%;background:var(--blue);border:3px solid var(--white);color:var(--white);text-align:center;font-weight:700;font-size:20px;line-height:20px;padding-top:9px}
.badge-off small{display:block;font-size:10px;line-height:12px}
.mini-item{left:151px;width:190px;display:flex;gap:10px;font-size:12.5px}
.mini-item .thumb{width:46px;height:36px;background:linear-gradient(90deg,#cfd6dc,#7d8891,#cfd6dc);border:1px solid #ddd;flex:none;margin-top:10px}
.mini-item .name{line-height:18px}
.mini-item .price{font-size:11px;line-height:22px}
.see-all{left:276px;top:1902px;font-size:13px}

/* products */
.section-title{font-family:"Roboto Slab",Georgia,serif;font-weight:700;font-size:14px;color:var(--green)}
.arrows{left:1000px;top:669px;display:flex;gap:6px}
.arrows i{width:17px;height:17px;border-radius:50%;background:#8a8a8a;display:block;position:relative}
.card{width:216px;background:var(--white);border:4px solid var(--card-border);overflow:hidden}
.card .corner{position:absolute;left:0;top:0;width:0;height:0;border-top:46px solid #e2e2e2;border-right:46px solid transparent}
.card .corner span{position:absolute;left:3px;top:-40px;transform:rotate(-45deg);font-size:11px;color:#444;font-style:italic}
.card .img{position:absolute;left:8px;width:192px}
.card .name{position:absolute;left:0;width:100%;text-align:center;font-size:13.5px;color:var(--text-dark)}
.card .price{position:absolute;left:0;width:100%;text-align:center;font-size:16px;font-weight:700;color:var(--text-dark)}
.price .old{color:var(--red);text-decoration:line-through}
.fish-grey{background:radial-gradient(ellipse at 50% 50%,#5f6b70 0,#8f9aa0 35%,#fff 70%)}
.fish-red{background:radial-gradient(ellipse at 50% 50%,#e45a5a 0,#f08a8a 40%,#fbe2e2 75%)}
.fish-tan{background:radial-gradient(ellipse at 50% 50%,#8b8a72 0,#b9b79c 35%,#fff 70%)}
.fish-blue{background:radial-gradient(ellipse at 50% 50%,#7b8fa3 0,#a9bccb 40%,#e9eef3 75%)}
.fish-cat{background:linear-gradient(160deg,#b7b2ad,#7b7774 55%,#9f9a95)}
.placeholder{background:#f3f3f3}

.info-box{left:362px;width:334px;border:4px solid var(--card-border);background:var(--white)}
.info-box .icon{left:18px}
.info-box .head{left:84px;font-family:"Roboto Slab",Georgia,serif;font-size:23px;color:var(--green);border-bottom:1px solid var(--green);padding-bottom:1px}
.info-box .text{left:84px;font-size:12.5px;color:var(--text-dark)}

.ad-box{left:761px;top:1033px;width:284px;height:237px;background:var(--lime);border:2px dashed #fff;outline:1px solid var(--lime)}
.ad-box .head{left:0;top:12px;width:100%;text-align:center;color:var(--white);font-family:"Montserrat",Arial,sans-serif;font-weight:700;font-size:25px;line-height:27px}
.coupon{border-radius:50%;background:var(--black);color:var(--white);text-align:center;font-family:"Montserrat",Arial,sans-serif;font-weight:700}
.ad-box .coupon{left:12px;top:72px;width:92px;height:92px;padding-top:12px;font-size:13px;line-height:15px}
.coupon b{display:block;font-size:30px;line-height:32px}
.ad-box .thumb{left:120px;top:72px;width:150px;height:92px;border:4px solid var(--black);background:linear-gradient(135deg,#c8a675,#e7d3b0 50%,#b94a3e)}
.ad-box .tag{left:0;top:170px;width:100%;text-align:center;color:var(--white);font-weight:700;font-size:14px}
.ad-bar{left:0;bottom:0;width:100%;height:38px;background:var(--black);display:flex;justify-content:space-between;align-items:center;padding:0 8px}
.brand-text{color:var(--white);font-family:"Montserrat",Arial,sans-serif;font-weight:700;font-size:17px;display:flex;align-items:center;gap:6px}
.brand-text i{width:12px;height:12px;background:var(--white);display:block}
.btn-order{background:#2f8fd8;color:var(--white);font-weight:700;font-size:14px;padding:3px 8px;border:1px solid #fff}

.wide-ad{left:254px;top:1978px;width:690px;height:84px;background:var(--lime);border:2px dashed #fff;outline:1px solid #ccc}
.wide-ad .coupon{left:14px;top:4px;width:72px;height:72px;padding-top:9px;font-size:10px;line-height:12px}
.wide-ad .coupon b{font-size:22px;line-height:24px}
.wide-ad .head{left:120px;top:6px;width:200px;text-align:center;color:var(--white);font-family:"Montserrat",Arial,sans-serif;font-weight:700;font-size:25px;line-height:24px}
.wide-ad .head small{display:block;color:var(--black);font-size:11px;line-height:16px}
.wide-ad .shot1{left:335px;top:10px;width:100px;height:60px;background:linear-gradient(180deg,#3b3b3b,#6fa8d8)}
.wide-ad .shot2{left:444px;top:10px;width:100px;height:60px;background:linear-gradient(135deg,#c8a675,#e7d3b0 50%,#b94a3e);border:3px solid var(--black)}
.wide-ad .right{left:555px;top:0;width:131px;height:80px;background:var(--black);display:flex;flex-direction:column;align-items:center;justify-content:center;gap:12px}

/* footer */
.footer{left:125px;top:2087px;width:949px;height:191px;background:var(--white);border:1px solid var(--line)}
.footer-inner{left:10px;top:10px;width:927px;height:169px;border:1px solid var(--line)}
.f-col{top:2116px}
.f-col h4{font-family:"Roboto Slab",Georgia,serif;font-weight:700;font-size:14px;color:var(--green);margin-bottom:8px}
.f-col ul{list-style:none}
.f-col li{font-size:11.5px;line-height:26.5px;padding-left:14px;position:relative}
.f-col li::before{content:"";position:absolute;left:2px;top:12px;width:4px;height:4px;border-radius:50%;background:#666}
.social{left:608px;top:2146px;display:flex;gap:12px}
.social i{width:30px;height:30px;border-radius:50%;background:#6b6b6b;display:block}
.cards{left:607px;top:2204px;display:flex;gap:9px}
.cards i{width:38px;height:23px;border:1px solid #ccc;display:block;border-radius:2px}
.bottom-links{left:125px;top:2289px;font-size:12px}
.copyright{left:820px;top:2289px;width:254px;text-align:right;font-size:12px}
.to-top{left:1155px;top:2276px;width:32px;height:32px;border-radius:50%;border:2px solid #888}
</style>
</head>
<body>
<div class="page">

  <!-- header -->
  <div class="abs logo"><span class="logo-mark"></span><span class="logo-name">PANTRYBASKET</span></div>
  <div class="abs search"><span>Search entire store here...</span>
    <svg width="16" height="16" viewBox="0 0 16 16"><circle cx="6.5" cy="6.5" r="5" fill="none" stroke="#3f8fd0" stroke-width="2"/><line x1="10" y1="10" x2="15" y2="15" stroke="#3f8fd0" stroke-width="2.4"/></svg>
  </div>
  <div class="abs cart-mini">
    <svg width="26" height="20" viewBox="0 0 26 20"><path d="M1 3h4l3 11h13l3-8H7" fill="none" stroke="#3f8fd0" stroke-width="2"/><circle cx="10" cy="17" r="2" fill="#3f8fd0"/><circle cx="19" cy="17" r="2" fill="#3f8fd0"/></svg>
    <span class="items">(0 item)</span><span class="sum">- ₦0.00</span>
    <svg width="10" height="6" viewBox="0 0 10 6"><path d="M0 0h10L5 6z" fill="#666"/></svg>
  </div>

  <!-- navigation -->
  <svg class="abs nav" viewBox="0 0 1002 52">
    <polygon points="0,0 36,0 36,52 12,52 0,26" fill="#4c8f1a"/>
    <rect x="35" y="0" width="950" height="50" fill="#6cb42c"/>
    <polygon points="984,0 992,0 1002,25 992,50 984,50" fill="#6cb42c"/>
    <polygon points="0,26 12,52 35,52 35,58" fill="#3f7d12"/>
  </svg>
  <nav class="abs nav-links">
    <a class="active" style="left:0">HOME</a>
    <a style="left:97px">HEALTH &amp; WELLNESS</a>
    <a style="left:290px">FRUITS &amp; VEGS</a>
    <a style="left:438px">POULTRY, MEAT &amp; FISH</a>
    <a style="left:647px">FOOD STUFFS</a>
    <a style="left:788px">RECIPES</a>
    <a style="left:886px">OTHERS</a>
  </nav>
  <div class="abs welcome">
    <span>Welcome to Pantrybasket.com. Feed well, live well</span>
    <span class="links">My Account <span>|</span> My Wishlist <span>|</span> My Cart <span>|</span> Checkout <span>|</span> Log In</span>
  </div>

  <div class="abs main"></div>

  <!-- hero slider -->
  <div class="abs slider">
    <div class="abs photo" role="img" aria-label="Wire shopping basket filled with fresh groceries"></div>
    <div class="abs headline">GROCERY<br><span class="teal">SHOPPING</span></div>
    <div class="abs sub-headline">In Affordable Price</div>
    <div class="abs btn-shop">SHOP NOW</div>
    <div class="abs dots"><i></i><i></i><i class="on"></i><i></i></div>
  </div>

  <div class="abs promo promo-delivery">
    <div class="abs title">FREE DELIVERY &amp; GET<br>10% DISCOUNT</div>
    <div class="abs note">On every Registered Users</div>
    <div class="abs strip">Read More...</div>
    <div class="abs seal">100%</div>
  </div>
  <div class="abs promo promo-spa">
    <div class="abs title">HERBAL &amp;AYURVEDIC<br>&amp; SPA PRODUCTS</div>
    <div class="abs photo" role="img" aria-label="Relaxing flower-petal spa bath"></div>
  </div>

  <!-- sidebar -->
  <div class="abs side-head blue" style="top:658px">CATEGORIES</div>
  <ul class="abs cat-list">
    <li>Health &amp; Wellness</li>
    <li>Fruits &amp; Vegs<span>+</span></li>
    <li>Poultry, Meat &amp; Fish<span>+</span></li>
    <li>Food Stuffs<span>+</span></li>
    <li>Recipes</li>
    <li>Others<span>+</span></li>
  </ul>

  <div class="abs side-head" style="top:908px">MY CART</div>
  <div class="abs side-note" style="top:962px">You have no items in your shopping cart.</div>

  <div class="abs side-head" style="top:1028px">COMPARE PRODUCTS</div>
  <div class="abs side-note" style="top:1083px">You have no items to compare.</div>

  <div class="abs hurry">
    <div class="abs title">Hurry Offer<br>Ends Soon</div>
    <div class="abs photo" role="img" aria-label="Fresh tomatoes, peppers, mushrooms and vegetables"></div>
    <div class="abs badge-off">50<small>%off</small></div>
  </div>

  <div class="abs side-head" style="top:1418px">LATEST PRODUCTS</div>
  <div class="abs mini-item" style="top:1474px"><div class="thumb" role="img" aria-label="Frozen tilapia"></div><div><div class="name">Frozen Tilapia (1kg)</div><div class="price">₦1,000.00</div><div>Add to Cart</div></div></div>
  <div class="abs mini-item" style="top:1563px"><div class="thumb" role="img" aria-label="Red snapper" style="background:linear-gradient(90deg,#f3c9c9,#e46262,#f3c9c9)"></div><div><div class="name">Red Snapper (1kg)</div><div class="price">₦1,000.00</div><div>Add to Cart</div></div></div>
  <div class="abs mini-item" style="top:1652px"><div class="thumb" role="img" aria-label="Frozen croacker"></div><div><div class="name">Frozen Croacker<br>(1kg)</div><div class="price">₦1,000.00</div><div>Add to Cart</div></div></div>
  <div class="abs mini-item" style="top:1761px"><div class="thumb" role="img" aria-label="Frozen argentina"></div><div><div class="name">Frozen Argentina<br>(1kg)</div><div class="price">₦1,000.00</div><div>Add to Cart</div></div></div>
  <div class="abs see-all">See All</div>

  <!-- latest products -->
  <div class="abs section-title" style="left:361px;top:668px">LATEST PRODUCTS</div>
  <div class="abs arrows">
    <i><svg width="17" height="17" viewBox="0 0 17 17"><path d="M10 4L6 8.5 10 13" fill="none" stroke="#fff" stroke-width="2"/></svg></i>
    <i><svg width="17" height="17" viewBox="0 0 17 17"><path d="M7 4l4 4.5L7 13" fill="none" stroke="#fff" stroke-width="2"/></svg></i>
  </div>

  <div class="abs card" style="left:362px;top:718px;height:296px">
    <div class="img fish-grey" style="top:40px;height:130px" role="img" aria-label="Frozen tilapia fish"></div>
    <div class="corner"><span>New</span></div>
    <div class="name" style="top:211px">Frozen Tilapia (1kg)</div>
    <div class="price" style="top:236px">₦1,000.00</div>
  </div>
  <div class="abs card" style="left:596px;top:718px;height:296px">
    <div class="img fish-red" style="top:46px;height:116px" role="img" aria-label="Red snapper fish"></div>
    <div class="corner"><span>New</span></div>
    <div class="name" style="top:211px">Red Snapper (1kg)</div>
    <div class="price" style="top:236px">₦1,000.00</div>
  </div>
  <div class="abs card" style="left:828px;top:718px;height:296px">
    <div class="img fish-tan" style="top:40px;height:130px" role="img" aria-label="Frozen croacker fish"></div>
    <div class="corner"><span>New</span></div>
    <div class="name" style="top:211px">Frozen Croacker (1kg)</div>
    <div class="price" style="top:236px">₦1,000.00</div>
  </div>

  <!-- info boxes -->
  <div class="abs info-box" style="top:1034px;height:96px">
    <svg class="abs icon" style="top:26px" width="56" height="36" viewBox="0 0 56 36"><rect x="0" y="4" width="34" height="22" fill="#888"/><path d="M34 10h12l8 9v7H34z" fill="#888"/><rect x="38" y="13" width="8" height="6" fill="#fff"/><circle cx="11" cy="29" r="5" fill="#666" stroke="#fff" stroke-width="2"/><circle cx="45" cy="29" r="5" fill="#666" stroke="#fff" stroke-width="2"/></svg>
    <div class="abs head" style="top:18px">FREE SHIPPING</div>
    <div class="abs text" style="top:53px">On Order Over <b>$30</b> offer today</div>
  </div>
  <div class="abs info-box" style="top:1167px;height:97px">
    <svg class="abs icon" style="top:20px" width="48" height="50" viewBox="0 0 48 50"><rect x="0" y="4" width="14" height="44" rx="3" fill="#888"/><rect x="16" y="12" width="30" height="36" rx="3" fill="#888"/><rect x="21" y="17" width="20" height="9" fill="#fff"/><g fill="#fff"><rect x="21" y="30" width="5" height="4"/><rect x="29" y="30" width="5" height="4"/><rect x="37" y="30" width="5" height="4"/><rect x="21" y="37" width="5" height="4"/><rect x="29" y="37" width="5" height="4"/><rect x="37" y="37" width="5" height="4"/></g></svg>
    <div class="abs head" style="top:18px">GIVE US CALL</div>
    <div class="abs text" style="top:53px">1-800-Pantry (1-800-555-0142)</div>
  </div>

  <!-- side ad -->
  <div class="abs ad-box">
    <div class="abs head">STILL NEED<br>A DESIGN?</div>
    <div class="abs coupon">FREE<b>$40</b>COUPON</div>
    <div class="abs thumb" role="img" aria-label="Sample design artwork"></div>
    <div class="abs tag">GET 50 TO 100+ BIDS IN 5 DAYS.</div>
    <div class="abs ad-bar"><span class="brand-text"><i></i>MakerBids</span><span class="btn-order">ORDER NOW</span></div>
  </div>

  <!-- featured products -->
  <div class="abs section-title" style="left:361px;top:1292px">FEATURED PRODUCTS</div>

  <div class="abs card" style="left:362px;top:1340px;height:280px">
    <div class="img fish-blue" style="top:30px;height:140px" role="img" aria-label="Two titus mackerel fish"></div>
    <div class="corner"><span>New</span></div>
    <div class="name" style="top:204px">Titus (1kg)</div>
    <div class="price" style="top:230px">₦1,000.00</div>
  </div>
  <div class="abs card" style="left:596px;top:1340px;height:280px">
    <div class="img placeholder" style="top:6px;height:182px" role="img" aria-label="Product image placeholder"></div>
    <div class="corner"><span>New</span></div>
    <div class="name" style="top:204px">Sawa (500g)</div>
    <div class="price" style="top:230px">₦1,000.00</div>
  </div>
  <div class="abs card" style="left:828px;top:1340px;height:280px">
    <div class="img placeholder" style="top:6px;height:182px" role="img" aria-label="Product image placeholder"></div>
    <div class="corner"><span>New</span></div>
    <div class="name" style="top:204px">Abodi (1kg)</div>
    <div class="price" style="top:230px">₦1,000.00</div>
  </div>

  <div class="abs card" style="left:362px;top:1640px;height:280px">
    <div class="img fish-cat" style="top:6px;height:178px" role="img" aria-label="Whole cat fish"></div>
    <div class="name" style="top:204px">Cat Fish (1kg)</div>
    <div class="price" style="top:230px"><span class="old">₦1,000.00</span> ₦950.00</div>
  </div>
  <div class="abs card" style="left:596px;top:1640px;height:280px">
    <div class="img fish-tan" style="top:36px;height:120px" role="img" aria-label="Fresh white croacker fish"></div>
    <div class="name" style="top:204px">Fresh White Croacker (1kg)</div>
    <div class="price" style="top:230px">₦1,000.00</div>
  </div>
  <div class="abs card" style="left:828px;top:1640px;height:280px">
    <div class="img placeholder" style="top:6px;height:182px" role="img" aria-label="Product image placeholder"></div>
    <div class="name" style="top:204px">Obokun (1kg)</div>
    <div class="price" style="top:230px">₦1,000.00</div>
  </div>

  <!-- wide ad -->
  <div class="abs wide-ad">
    <div class="abs coupon">FREE<b>$40</b>COUPON</div>
    <div class="abs head">STILL NEED<br>A DESIGN<small>HURRY LIMITED TIME OFFER</small></div>
    <div class="abs shot1" role="img" aria-label="Sample website design"></div>
    <div class="abs shot2" role="img" aria-label="Sample design artwork"></div>
    <div class="abs right"><span class="brand-text"><i></i>MakerBids</span><span class="btn-order">ORDER NOW</span></div>
  </div>

  <!-- footer -->
  <div class="abs footer"><div class="abs footer-inner"></div></div>
  <div class="abs f-col" style="left:151px"><h4>CUSTOMER SERVICE</h4><ul><li>About Us</li><li>Delivery Information</li><li>Privacy Policy</li><li>Term &amp; Condition</li></ul></div>
  <div class="abs f-col" style="left:379px"><h4>MY ACCOUNT</h4><ul><li>My Product</li><li>My Orders</li><li>My Address</li><li>My Personal Info</li></ul></div>
  <div class="abs f-col" style="left:607px"><h4>FOLLOW ME</h4></div>
  <div class="abs social"><i></i><i></i></div>
  <div class="abs cards">
    <i style="background:#fbe9b7"></i><i style="background:#f4f4f4"></i><i style="background:#1a3d8f"></i><i style="background:#eef1f8"></i>
  </div>

  <div class="abs bottom-links">Site Map | Search Terms | Advanced Search | Orders and Returns | Contact Us</div>
  <div class="abs copyright">© 2014 Pantrybasket.com Ltd</div>
  <div class="abs to-top">
    <svg width="28" height="28" viewBox="0 0 28 28"><path d="M8 17l6-6 6 6" fill="none" stroke="#888" stroke-width="2"/></svg>
  </div>

</div>
</body>
</html>
```